Rosko Tamblin

I am a songwriter and would like to include a bio, pictures, discography, CD covers and access to some of my music

Target Market(s)

Music Lovers, songwriters publishers

Coding

Coded - Design and coding required

Number of Pages Required

5+ page

Requirements
Must have
• Pictures of my CD covers, pictures of me and either my Music or links to my music
Nice to have
Should not have
• cartoons

```html
<!DOCTYPE html>
<html lang="en">
<head>
<meta charset="utf-8">
<title>Rosko Tamblin</title>
<link rel="stylesheet" href="https://fonts.googleapis.com/css2?family=Abril+Fatface&family=Lato:wght@400;700&display=swap">
<style>
:root{
  --orange:#ff6a3d;
  --ink:#111111;
  --text:#2a2a2a;
  --rule:#d9d9d9;
  --white:#ffffff;
  --dark-panel:rgba(10,8,6,0.82);
}
*{margin:0;padding:0;box-sizing:border-box}
html,body{width:1200px;height:3342px;overflow:hidden;background:var(--white)}
body{position:relative;font-family:'Lato',sans-serif;color:var(--text)}
.abs{position:absolute}
.display{font-family:'Abril Fatface',serif;color:var(--ink);font-weight:400}
.site-header{left:0;top:0;width:1200px;height:108px;background:var(--white)}
.brand{left:74px;top:30px;font-size:39px;line-height:48px}
.nav a{position:absolute;top:44px;font-family:'Abril Fatface',serif;font-size:19px;color:var(--ink);text-decoration:none;white-space:nowrap}
.nav a.active{color:var(--orange)}
.nav-marker{left:608px;top:104px;width:48px;height:4px;background:var(--orange)}
.nav-tri{left:624px;top:98px;width:0;height:0;border-left:8px solid transparent;border-right:8px solid transparent;border-bottom:7px solid var(--orange)}
.hero{left:0;top:108px;width:1200px;height:577px;background:radial-gradient(ellipse at 55% 60%,#ff9a2a 0%,#e0520f 25%,#7a1f05 50%,#1f0a04 75%,#0a0605 100%)}
.hero-card{left:105px;top:319px;width:503px;height:188px;background:var(--dark-panel);padding:26px 28px}
.hero-card h1{font-family:'Abril Fatface',serif;font-weight:400;color:var(--white);font-size:58px;line-height:70px}
.hero-card p{color:var(--white);font-size:20px;line-height:24px;margin-top:10px;max-width:400px}
.hero-chevron{left:588px;top:602px}
.section-title{font-size:60px;line-height:70px}
.title-rule{height:3px;width:89px;background:var(--orange)}
.bio-text{left:75px;top:852px;width:522px;font-size:15.5px;letter-spacing:0.25px;line-height:27.8px}
.btn{display:flex;align-items:center;justify-content:center;background:var(--orange);color:var(--white);font-family:'Abril Fatface',serif;border-radius:24px}
.review{left:881px;width:245px}
.review p{font-size:15px;letter-spacing:0.2px;line-height:28px;padding-left:6px}
.review .name{font-family:'Abril Fatface',serif;font-size:16px;color:var(--ink);padding-left:5px}
.stars{padding-left:5px}
.review-rule{height:1px;background:var(--rule);width:245px}
.caption{font-size:30px;line-height:38px}
.cd-copy{left:798px;top:2198px;width:350px;font-size:25px;line-height:28.5px;color:var(--ink)}
.site-footer{left:0;top:3044px;width:1200px;height:298px;background:var(--ink);color:var(--white);text-align:center}
.footer-brand{font-family:'Abril Fatface',serif;font-size:40px;margin-top:40px}
.footer-nav{margin-top:18px;display:flex;justify-content:center;gap:30px}
.footer-nav a,.social a{color:var(--white);text-decoration:none}
.footer-nav a{font-family:'Abril Fatface',serif;font-size:18px}
.social{margin-top:26px;display:flex;justify-content:center;gap:26px;font-size:17px;font-weight:700}
.copyright{margin-top:30px;font-size:14px}
</style>
</head>
<body>

<header class="site-header abs">
  <div class="brand display abs">Rosko Tamblin</div>
  <nav class="nav">
    <a class="active" style="left:620px">Bio</a>
    <a style="left:678px">Discography</a>
    <a style="left:814px">CD covers</a>
    <a style="left:929px">Gallery</a>
    <a style="left:1025px">Contact Me</a>
  </nav>
  <div class="nav-marker abs"></div>
  <div class="nav-tri abs"></div>
</header>

<section class="hero abs" role="img" aria-label="Portrait of the songwriter standing before a glowing fiery crater at night"></section>
<div class="hero-card abs">
  <h1>Rosko Tamblin</h1>
  <p>In the late 70s and early 80s Tamblin began writing music again.</p>
</div>
<svg class="hero-chevron abs" width="24" height="16" viewBox="0 0 24 16"><polyline points="4,4 12,12 20,4" fill="none" stroke="#fff" stroke-width="3"/></svg>

<!-- Bio -->
<h2 class="section-title display abs" style="left:76px;top:726px">Bio</h2>
<div class="title-rule abs" style="left:74px;top:799px"></div>
<p class="bio-text abs">Rosko Tamblin was born and raised in Houston, Texas. He began playing music at the age of eight when his sister returned home from summer camp and asked her parents to buy her a baritone ukulele. She taught her younger brother some chords on the ukulele and he was hooked. The following spring, they went to one of the border towns in Mexico and bought a Mexican guitar for $12. They restrung it with nylon strings and Tamblin began to learn how to play the guitar. He took guitar lessons at a local music store and learned how to play the hits of the day by groups like the Tollbridge Five, the Marlowes, and the Fenwicks. He got his first electric guitar when he was about 10 years old. He began jamming with other musicians when he was 13 or 14. They were much more experienced than he and introduced him to the blues.</p>
<div class="btn abs" style="left:74px;top:1206px;width:135px;height:44px;font-size:16px">Read more</div>

<div class="abs" style="left:623px;top:862px;width:214px;height:312px;background:var(--orange)"></div>
<div class="abs" style="left:641px;top:844px;width:214px;height:312px;background:linear-gradient(180deg,#a9b89a 0%,#d8d4c4 45%,#f2f1ec 70%,#8a8a72 100%)" role="img" aria-label="Photo of the songwriter outdoors wearing a straw hat and white shirt"></div>

<!-- Review -->
<h2 class="section-title display abs" style="left:881px;top:726px">Review</h2>
<div class="title-rule abs" style="left:881px;top:799px"></div>
<div class="review abs" style="top:849px">
  <svg class="stars" width="130" height="16" viewBox="0 0 130 16">
    <defs><polygon id="star" points="8,0 10,5.5 16,6 11.5,10 13,16 8,12.7 3,16 4.5,10 0,6 6,5.5" fill="#ff6a3d"/></defs>
    <use href="#star" x="0"/><use href="#star" x="26"/><use href="#star" x="52"/><use href="#star" x="78"/><use href="#star" x="104"/>
  </svg>
  <p style="margin-top:4px">Jazz-funk-rock fusion - just right up my alley! Great tune and groove, I had fun arranging piano and electric piano lines for it.</p>
  <div class="name" style="margin-top:8px">Carla Venturi</div>
  <div class="review-rule" style="margin-top:12px"></div>
  <svg class="stars" style="margin-top:18px" width="130" height="16" viewBox="0 0 130 16">
    <use href="#star" x="0"/><use href="#star" x="26"/><use href="#star" x="52"/><use href="#star" x="78"/><use href="#star" x="104"/>
  </svg>
  <p style="margin-top:6px">A real pleasure working on Rosko's nice music</p>
  <div class="name" style="margin-top:6px">Arbor Sound Studio</div>
  <div class="review-rule" style="margin-top:14px"></div>
</div>
<div class="btn abs" style="left:881px;top:1206px;width:245px;height:46px;font-size:20px">More Reviews</div>

<!-- Discography -->
<h2 class="section-title display abs" style="left:76px;top:1314px">Discography</h2>
<div class="title-rule abs" style="left:74px;top:1389px"></div>
<div class="abs" style="left:75px;top:1462px;width:253px;height:241px;background:linear-gradient(160deg,#2c2f5a 0%,#6a6fa0 40%,#1a1a2a 70%,#b2401c 100%)" role="img" aria-label="Album front cover with lightning storm and silhouetted figure"></div>
<div class="abs" style="left:341px;top:1462px;width:253px;height:241px;background:linear-gradient(180deg,#c9cbd8 0%,#e7e8ee 50%,#aeb0c0 100%)" role="img" aria-label="Album back cover with track listing"></div>
<div class="caption display abs" style="left:77px;top:1728px">Lorem ipsum dolor sit amet,<br>consectetur adipiscing</div>
<div class="caption display abs" style="left:625px;top:1454px">Lorem ipsum dolor sit amet,<br>consectetur adipiscing</div>
<div class="abs" style="left:607px;top:1554px;width:253px;height:242px;background:linear-gradient(180deg,#6b7f8e 0%,#c9d4da 40%,#3d4c55 75%,#a3631a 100%)" role="img" aria-label="Album front cover with crashing ocean waves"></div>
<div class="abs" style="left:873px;top:1554px;width:253px;height:242px;background:linear-gradient(160deg,#3a2a14 0%,#a0521a 45%,#d89a5a 70%,#5a2a10 100%)" role="img" aria-label="Album back cover with seashell artwork and song titles"></div>

<!-- CD Covers -->
<h2 class="section-title display abs" style="left:76px;top:1934px">CD Covers</h2>
<div class="title-rule abs" style="left:74px;top:2009px"></div>
<svg class="abs" style="left:360px;top:2070px" width="420" height="420" viewBox="0 0 420 420" role="img" aria-label="CD disc printed with colourful swirling artwork">
  <defs><radialGradient id="disc" cx="0.4" cy="0.5" r="0.6"><stop offset="0" stop-color="#f25a7a"/><stop offset="0.5" stop-color="#7a3ac0"/><stop offset="1" stop-color="#39b4d8"/></radialGradient></defs>
  <circle cx="211" cy="209" r="204" fill="url(#disc)"/>
  <circle cx="211" cy="209" r="54" fill="#ffffff"/>
  <circle cx="211" cy="209" r="42" fill="#dcdcdc"/>
</svg>
<div class="abs" style="left:75px;top:2054px;width:489px;height:451px;background:linear-gradient(135deg,#e8505a 0%,#f08a4a 30%,#7ec06a 50%,#6a4ac0 75%,#2ab0d8 100%);box-shadow:2px 3px 6px rgba(0,0,0,0.25)" role="img" aria-label="CD front cover showing a musician with a mandolin on a psychedelic swirl"></div>
<p class="cd-copy abs">Sed ut perspiciatis unde omnis iste natus error sit voluptatem accusantium doloremque laudantium,a</p>
<div class="btn abs" style="left:813px;top:2338px;width:245px;height:46px;font-size:20px">MY MUSIC</div>

<!-- Gallery -->
<h2 class="section-title display abs" style="left:76px;top:2590px">Gallery</h2>
<div class="title-rule abs" style="left:74px;top:2665px"></div>
<div class="abs" style="left:82px;top:2713px;width:282px;height:259px;background:linear-gradient(160deg,#1a1208 0%,#e05a10 35%,#c8b89a 65%,#2a2a2a 100%)" role="img" aria-label="Album art with a burning table setting"></div>
<div class="abs" style="left:367px;top:2713px;width:416px;height:259px;background:linear-gradient(135deg,#f7b8a0 0%,#f59a7a 50%,#f8c0a8 100%)" role="img" aria-label="Album art with a faded childhood photo"></div>
<div class="abs" style="left:786px;top:2713px;width:281px;height:259px;background:linear-gradient(180deg,#f06aa0 0%,#b86ad8 45%,#6ab0e8 100%)" role="img" aria-label="Album back cover with song list on a pink and blue wash"></div>
<div class="abs" style="left:1070px;top:2713px;width:130px;height:259px;background:linear-gradient(180deg,#1a1a10 0%,#d83a10 30%,#2a6a20 70%,#0a2a0a 100%)" role="img" aria-label="Album art with a forest scene"></div>
<svg class="abs" style="left:1110px;top:2836px" width="20" height="30" viewBox="0 0 20 30"><polyline points="4,3 16,15 4,27" fill="none" stroke="#fff" stroke-width="3"/></svg>

<!-- Footer -->
<footer class="site-footer abs">
  <div class="footer-brand">Rosko Tamblin</div>
  <nav class="footer-nav">
    <a>Bio</a><a>Discography</a><a>CD covers</a><a>Gallery</a><a>Contact Me</a>
  </nav>
  <div class="social"><a>Folio</a><a>Chirp</a><a>Snapframe</a><a>Linkwork</a></div>
  <p class="copyright">© 2020 |&nbsp; www.companyname.com</p>
</footer>

</body>
</html>
```